1876 Basins & Spouts Business Card

I'm wanting to get a business card designed. Our business is 1876 Basins & Spouts
Details for the card:

1876 Basins & Spouts
Name: Harold Vesk
Email: harold@1876basinsandspouts.com.au
Website: www.1876basinsandspouts.com.au
Mobile: 0438 260 947
Phone: 02 7481 3926

Font of Basins & Spouts is called Snell Roundhand. Not sue what font logo text is.

I'm thinking two sided but it doesn't have to be.

```html
<!DOCTYPE html>
<html lang="en">
<head>
<meta charset="utf-8">
<title>1876 Basins &amp; Spouts – Business Card</title>
<link href="https://fonts.googleapis.com/css2?family=Lato:wght@400&family=Montserrat:wght@500&display=swap" rel="stylesheet">
<style>
  :root {
    --page-bg: #2a2a2a;
    --card-white: #ffffff;
    --ink: #222222;
    --ink-soft: #555555;
    --back-base: #979797;
    --tile-a: #a9a9a7;
    --tile-b: #b3b0ab;
    --tile-c: #a7a5a2;
    --tile-d: #aeaeac;
    --tile-e: #a4a4a2;
    --tile-f: #acaaa6;
    --tile-g: #9f9a8c;
    --tile-h: #b0b0ae;
    --mark-white: #ffffff;
  }
  * { box-sizing: border-box; margin: 0; padding: 0; }
  html, body { width: 1200px; height: 900px; overflow: hidden; }
  body {
    background: var(--page-bg);
    font-family: "Lato", Arial, sans-serif;
    color: var(--ink);
    position: relative;
  }
  .card {
    position: absolute;
    left: 261px;
    width: 656px;
    height: 358px;
    box-shadow: 0 3px 10px rgba(0,0,0,0.45);
  }
  .card--front { top: 69px; background: var(--card-white); }
  .card--back { top: 472px; background: var(--back-base); }

  .brand {
    position: absolute;
    left: 30px;
    top: 44px;
    display: flex;
    align-items: center;
    gap: 12px;
  }
  .brand__dot {
    width: 14px; height: 14px; border-radius: 50%;
    background: var(--ink);
  }
  .brand__name {
    font-family: "Lato", Arial, sans-serif;
    font-weight: 400;
    font-size: 24px;
    color: var(--ink);
  }
  .brand__tagline {
    position: absolute;
    left: 117px;
    top: 84px;
    font-size: 8px;
    color: var(--ink-soft);
    white-space: nowrap;
  }

  .contact {
    position: absolute;
    left: 324px;
    top: 139px;
  }
  .contact__name {
    font-family: "Montserrat", Arial, sans-serif;
    font-weight: 500;
    font-size: 28px;
    letter-spacing: 2.8px;
    line-height: 1.1;
  }
  .contact__role { font-size: 16px; letter-spacing: 0.6px; line-height: 1.2; }
  .contact__address {
    font-size: 16px; letter-spacing: 0.9px; line-height: 21px; margin-top: 12px;
    font-style: normal;
  }
  .contact__list { list-style: none; margin-top: 9px; }
  .contact__item {
    display: flex; align-items: center; gap: 8px;
    font-size: 16px; letter-spacing: 0.9px; line-height: 21.5px;
    white-space: nowrap;
  }
  .contact__icon { width: 12px; height: 12px; flex: none; }

  .gallery__tile { position: absolute; }
  .back-mark {
    position: absolute;
    left: 0; right: 0; top: 160px;
    display: flex; justify-content: center; align-items: center; gap: 12px;
  }
  .back-mark__dot { width: 16px; height: 16px; border-radius: 50%; background: var(--mark-white); }
  .back-mark__name {
    font-family: "Lato", Arial, sans-serif;
    font-weight: 400;
    font-size: 30px;
    color: var(--mark-white);
  }
</style>
</head>
<body>

<section class="card card--front" aria-label="Card front">
  <div class="brand">
    <span class="brand__dot"></span>
    <span class="brand__name">1876 Basins &amp; Spouts</span>
  </div>
  <p class="brand__tagline">Pairing classic character with everyday function</p>

  <div class="contact">
    <h1 class="contact__name">HAROLD VESK</h1>
    <p class="contact__role">Director</p>
    <address class="contact__address">PO Box 41 Mount<br>Alder NSW 2793</address>
    <ul class="contact__list">
      <li class="contact__item">
        <svg class="contact__icon" viewBox="0 0 12 12" aria-hidden="true"><path d="M2.5 0.8 L4.3 0.8 L4.8 3.4 L3.7 4.3 C4.3 6 5.6 7.4 7.5 8.2 L8.4 7.1 L11 7.7 L11 9.5 C11 10.4 10.3 11 9.4 11 C5.2 10.6 1.4 6.9 1 2.4 C1 1.5 1.6 0.8 2.5 0.8 Z" fill="none" stroke="#222" stroke-width="1.1"/></svg>
        <span>0438 260 947</span>
      </li>
      <li class="contact__item">
        <svg class="contact__icon" viewBox="0 0 12 12" aria-hidden="true"><rect x="2.5" y="0.6" width="7" height="10.8" rx="1.2" fill="none" stroke="#222" stroke-width="1.2"/><circle cx="6" cy="9.5" r="0.7" fill="#222"/></svg>
        <span>02 7481 3926</span>
      </li>
      <li class="contact__item">
        <svg class="contact__icon" viewBox="0 0 12 12" aria-hidden="true"><rect x="0.6" y="2.2" width="10.8" height="7.6" rx="0.8" fill="none" stroke="#222" stroke-width="1.1"/><path d="M0.8 2.6 L6 6.6 L11.2 2.6" fill="none" stroke="#222" stroke-width="1.1"/></svg>
        <span>harold@1876basinsandspouts.com.au</span>
      </li>
      <li class="contact__item">
        <svg class="contact__icon" viewBox="0 0 12 12" aria-hidden="true"><g fill="none" stroke="#222" stroke-width="1"><circle cx="6" cy="6" r="5.3"/><ellipse cx="6" cy="6" rx="2.3" ry="5.3"/><path d="M0.7 6 H11.3 M1.5 3.4 H10.5 M1.5 8.6 H10.5"/></g></svg>
        <span>www.1876basinsandspouts.com.au</span>
      </li>
    </ul>
  </div>
</section>

<section class="card card--back" aria-label="Card back">
  <div class="gallery__tile" style="left:6px;top:5px;width:129px;height:169px;background:linear-gradient(180deg,#b5b5b3,var(--tile-a) 60%,#8a8a88)" role="img" aria-label="Photo of a white kitchen corner with a gas range"></div>
  <div class="gallery__tile" style="left:145px;top:5px;width:177px;height:169px;background:linear-gradient(180deg,#a8998a,var(--tile-b) 45%,#b5b5b3)" role="img" aria-label="Photo of copper pendant lights over a vase of autumn leaves"></div>
  <div class="gallery__tile" style="left:331px;top:5px;width:177px;height:169px;background:linear-gradient(180deg,#b2b2b0,var(--tile-c) 70%,#8f8d8a)" role="img" aria-label="Photo of a laundry with a farmhouse sink and washing machine"></div>
  <div class="gallery__tile" style="left:518px;top:5px;width:133px;height:169px;background:linear-gradient(180deg,#b6b8b4,var(--tile-d) 55%,#a39e98)" role="img" aria-label="Photo of a white sink under wide windows"></div>
  <div class="gallery__tile" style="left:6px;top:184px;width:129px;height:168px;background:linear-gradient(180deg,#b4b4b2,var(--tile-e) 65%,#7c7670)" role="img" aria-label="Photo of a white kitchen island with metal stools"></div>
  <div class="gallery__tile" style="left:145px;top:184px;width:177px;height:168px;background:linear-gradient(180deg,#b2b1ae,var(--tile-f) 60%,#a09a90)" role="img" aria-label="Photo of a white kitchen with open shelves and an oven"></div>
  <div class="gallery__tile" style="left:331px;top:184px;width:177px;height:168px;background:linear-gradient(180deg,#b1b1b1,var(--tile-g) 55%,#7a86a8)" role="img" aria-label="Photo of a brass tap beside blue hydrangeas"></div>
  <div class="gallery__tile" style="left:518px;top:184px;width:133px;height:168px;background:linear-gradient(180deg,#a8aba4,var(--tile-h) 55%,#bcbcba)" role="img" aria-label="Photo of a brass tap running into a white sink with flowers"></div>

  <div class="back-mark">
    <span class="back-mark__dot"></span>
    <span class="back-mark__name">1876 Basins &amp; Spouts</span>
  </div>
</section>

</body>
</html>
```